Gift Cards in the Mail Envelope

Mailing out gift cards in the envelope. Need an eye popping envelope. Please look at the enclosed images. The envelope should look like that.

Low design quality

```html
<!DOCTYPE html>
<html lang="en">
<head>
<meta charset="utf-8">
<title>Gift Voucher Envelope</title>
<link href="https://fonts.googleapis.com/css2?family=Amatic+SC:wght@700&family=Montserrat:wght@400&display=swap" rel="stylesheet">
<style>
  :root {
    --backdrop: #767873;
    --envelope: #e8e835;
    --fold-line: #cfcf2a;
    --ink: #262626;
  }
  * { margin: 0; padding: 0; box-sizing: border-box; }
  html, body {
    width: 1200px;
    height: 982px;
    overflow: hidden;
    background: var(--backdrop);
  }
  .canvas {
    position: relative;
    width: 1200px;
    height: 982px;
  }
  .envelope {
    position: absolute;
    top: 363px;
    width: 332px;
    height: 228px;
    background: var(--envelope);
  }
  .envelope--front { left: 252px; }
  .envelope--back { left: 627px; }

  .front-title {
    position: absolute;
    left: 0;
    width: 100%;
    top: 64px;
    text-align: center;
    font-family: "Amatic SC", cursive;
    font-weight: 700;
    font-size: 58px;
    line-height: 1;
    letter-spacing: 1px;
    color: var(--ink);
  }
  .front-subtitle {
    position: absolute;
    left: 0;
    width: 100%;
    top: 130px;
    text-align: center;
    font-family: "Montserrat", sans-serif;
    font-size: 13px;
    color: var(--ink);
  }
  .envelope-folds {
    position: absolute;
    inset: 0;
  }
  .flap-value {
    position: absolute;
    left: 0;
    width: 100%;
    top: 51px;
    text-align: center;
    font-family: "Amatic SC", cursive;
    font-weight: 700;
    font-size: 25px;
    line-height: 1;
    color: var(--ink);
  }
  .flap-prompt {
    position: absolute;
    left: 0;
    width: 100%;
    top: 75px;
    text-align: center;
    font-family: "Montserrat", sans-serif;
    font-size: 6.5px;
    color: var(--ink);
  }
</style>
</head>
<body>
  <main class="canvas">
    <section class="envelope envelope--front">
      <h1 class="front-title">Gift Voucher</h1>
      <p class="front-subtitle">It’s inside the envelope</p>
    </section>

    <section class="envelope envelope--back">
      <svg class="envelope-folds" width="332" height="228" viewBox="0 0 332 228" aria-hidden="true">
        <path d="M1 3 L34 82 Q37 88 45 88 L287 88 Q295 88 298 82 L331 3"
              fill="none" stroke="var(--fold-line)" stroke-width="0.8"/>
        <line x1="35" y1="88" x2="2" y2="227" stroke="var(--fold-line)" stroke-width="0.8"/>
        <line x1="297" y1="88" x2="330" y2="227" stroke="var(--fold-line)" stroke-width="0.8"/>
      </svg>
      <p class="flap-value">$100</p>
      <p class="flap-prompt">Open me!</p>
    </section>
  </main>
</body>
</html>
```